Commercial Cleaning Company Website Design

We are working with Harbor Tidy Team. They are a commercial cleaning company that needs a new website design.

Some sites to use for inspiration:

https://www.plenvask.com
https://gleam-panecare.com
https://tidwellhelpers.net
https://quietnesthouse.com
https://www.thedustingbureau.com
https://www.pennytidy.com

Thank you for taking the time to consider designing a website for us. We are web developers based in Stockton and Los Angeles, CA, USA. Most of our projects go through the same process. Understanding this process may help you win a project with us. We custom-code all of our websites in-house. We don’t have any requirements as to what tools you use for your design, but we prefer Figma files. For any design that we label as four-stars, we send it to the client for review. The client picks the final design they want us to use. Once we complete this process, we will continue to show additional clients all the four-star sites and purchase them later. Your designs will have multiple chances to sell. For better chances of success, we ask that you follow these guidelines.

IMAGES:
If you use any images or icons in the design, we ask that you have a link to the asset so we can purchase the image/icon. Most of the designs we submit do not have the customer’s images on them unless they have some great images. Be creative; show us the feeling you are trying to portray with your image choices. Use any royalty-free site you choose. We subscribe to Adobe and mainly use their images, but we can purchase images outside of Adobe.

PLEASE NOTE: we will not submit designs to clients with watermarks on the images.

FONTS:
We ask that you identify the fonts used in the design. This can be done in a message if you want. We typically use Google Fonts and Adobe Fonts.

CONTENT:
We're always open to different content and ideas. We often submit designs with stock images so the client can see our vision. We typically take pictures after the website launch to use their images with our vision. Lorem Ipsum is fine for paragraphs, but we ask that you write the headers in correct English. We want to be able to show the vision and identify the sections of the website.

INSPIRATION:
We typically add a couple of links in the brief of websites we like to help you get started in your design.

REVISIONS:
We do not often ask for revisions of the designs unless we see something in the design that may not appeal to the client. If there are slight changes that we want to make, we do that in the development process.

FEEDBACK:
We rarely give feedback on designs during the design process. We are working on many website projects and do not have the time to provide feedback. We usually respond if your request is well thought out and asks specific questions, but a note asking “feedback, please” usually goes unanswered.

```html
<!DOCTYPE html>
<html lang="en">
<head>
<meta charset="utf-8">
<title>Harbor Tidy Team – Commercial Cleaning</title>
<link href="https://fonts.googleapis.com/css2?family=Poppins:ital,wght@0,400;0,500;0,600;0,700;0,800;1,400&display=swap" rel="stylesheet">
<style>
:root{
  --blue:#1f4fc3;
  --blue-dark:#163e9e;
  --orange:#f04a1c;
  --yellow:#ffaa00;
  --ink:#1c1c1c;
  --text:#3d3d3d;
  --soft:#eef2f8;
  --field:#f1f2f5;
  --white:#ffffff;
}
*{box-sizing:border-box;margin:0;padding:0}
html,body{width:1200px;height:4648px;overflow:hidden}
body{position:relative;background:var(--white);font-family:"Poppins",sans-serif;color:var(--ink)}
.abs{position:absolute}
.btn{position:absolute;display:flex;align-items:center;justify-content:center;background:var(--orange);color:var(--white);font-weight:600;font-size:11px;border-radius:20px;text-transform:uppercase;letter-spacing:.2px}
.ph{position:absolute;overflow:hidden}
.section-title{position:absolute;left:0;width:1200px;text-align:center;font-weight:700;font-size:38px;color:var(--ink)}

/* header */
.topbar{top:10px;left:860px;display:flex;font-size:10px;color:#333}
.topbar span{padding:0 14px;border-left:1px solid #ccc}
.topbar span:first-child{border-left:none}
.topline{top:33px;left:530px;width:670px;height:1px;background:#e3e3e3}
.brand{display:flex;align-items:center;gap:10px}
.brand-dot{width:22px;height:22px;border-radius:50%;background:var(--orange)}
.brand-name{font-weight:700;font-size:19px;letter-spacing:4px;color:var(--blue);line-height:1}
.nav{top:58px;left:528px;display:flex;align-items:center;font-size:12.5px;font-weight:500;color:#222}
.nav span{margin-right:34px}

/* hero */
.hero{top:103px;left:0;width:1200px;height:560px;background:linear-gradient(120deg,#3b66cf 0%,#2453c2 55%,#3a6bd6 100%)}
.hero-title{top:222px;left:90px;font-weight:800;font-size:56px;line-height:61px;color:var(--white)}
.hero-title em{font-style:normal;color:var(--yellow)}
.hero-sub{top:416px;left:90px;font-size:13.5px;color:var(--white)}

/* features */
.feature{width:168px;height:168px;border-radius:50%;display:flex;flex-direction:column;align-items:center;justify-content:center;color:var(--white);font-weight:600;font-size:12.5px;text-align:center;line-height:16px}
.feature svg{margin-bottom:12px}
.feature .chev{position:absolute;bottom:-8px;left:74px;width:20px;height:20px;border-radius:50%;background:var(--white);box-shadow:0 2px 5px rgba(0,0,0,.15)}

/* about */
.eyebrow{font-weight:600;font-size:19px}
.about-title{font-weight:700;font-size:38px}
.body-text{font-size:13.5px;line-height:21.5px;color:var(--text)}

/* why */
.why-item{left:94px;width:466px;height:74px;border:1.5px solid #d9dbe1;border-radius:6px;display:flex;align-items:center;font-weight:600;font-size:15px;padding:6px}
.why-item .ico{width:82px;height:60px;border-radius:4px;display:flex;align-items:center;justify-content:center;margin-right:20px}
.why-item.active{background:var(--blue);border-color:var(--blue);color:var(--white)}

/* services */
.card{top:2303px;width:251px;height:309px;background:var(--white);border-radius:6px;box-shadow:0 4px 18px rgba(30,60,120,.08);padding:22px 20px 0}
.card h3{font-size:15px;font-weight:600}
.card .go{position:absolute;top:16px;right:20px;width:34px;height:34px;border-radius:50%;background:#e5f5e8;display:flex;align-items:center;justify-content:center}
.card hr{border:none;border-top:1.5px solid #e5e5e5;margin:20px 0 22px}
.card p{font-size:11.5px;line-height:19px;color:var(--text)}
.card .ph{left:20px;bottom:16px;width:211px;height:134px;border-radius:4px}

/* how */
.step-ico{width:84px;height:84px;border-radius:50%;display:flex;align-items:center;justify-content:center;border:5px solid var(--white);box-shadow:0 4px 12px rgba(0,0,0,.12)}
.step h4{font-size:14.5px;font-weight:600;margin-bottom:6px}
.step p{font-size:11px;line-height:14.5px;color:var(--text);width:260px}

/* contact */
.field{position:absolute;height:40px;background:var(--field);border-radius:20px;font-size:11px;color:#333;padding:13px 20px}

/* footer */
.footer{top:4250px;left:0;width:1200px;height:398px;background:var(--blue)}
.f-head{font-size:21px;font-weight:600;color:var(--white)}
.f-row{display:flex;align-items:center;gap:12px;font-size:14px;color:var(--white)}
.f-ico{width:26px;height:26px;border-radius:50%;background:var(--orange);display:flex;align-items:center;justify-content:center}
</style>
</head>
<body>

<!-- Header -->
<div class="abs brand" style="top:24px;left:90px">
  <div class="brand-dot"></div>
  <div class="brand-name">HARBOR TIDY TEAM</div>
</div>
<div class="abs topbar"><span>Blog</span><span>Contact</span><span>Careers</span><span>New Clients</span></div>
<div class="abs topline"></div>
<div class="abs nav">
  <svg width="14" height="14" viewBox="0 0 24 24" style="margin-right:22px"><path d="M12 3 2 12h3v8h5v-5h4v5h5v-8h3z" fill="#f04a1c"/></svg>
  <span>Services</span><span>About Us</span><span>Testimonials</span>
  <svg width="12" height="12" viewBox="0 0 24 24" style="margin-right:6px"><path d="M6.6 10.8a15 15 0 0 0 6.6 6.6l2.2-2.2c.3-.3.7-.4 1-.2 1.1.4 2.3.6 3.6.6.6 0 1 .4 1 1V20c0 .6-.4 1-1 1A17 17 0 0 1 3 4c0-.6.4-1 1-1h3.5c.6 0 1 .4 1 1 0 1.3.2 2.5.6 3.6.1.3 0 .7-.2 1z" fill="#f04a1c"/></svg>
  <span style="font-weight:600;margin-right:22px">(123) 456-7890</span>
</div>
<div class="btn" style="top:52px;left:995px;width:116px;height:34px;font-size:10.5px">Contact Us</div>

<!-- Hero -->
<section class="abs hero"></section>
<div class="ph" role="img" aria-label="Cleaner mopping a polished floor" style="top:166px;left:722px;width:390px;height:390px;border-radius:50%;background:linear-gradient(150deg,#d9d4cc,#9a958c 60%,#5f6d7a)"></div>
<h1 class="abs hero-title">Professional<br>Commercial <em>Cleaning</em><br>You Can Trust</h1>
<p class="abs hero-sub">Reliable, Efficient, and Affordable Cleaning Solutions for Your Business.</p>
<div class="btn" style="top:460px;left:90px;width:158px;height:32px;font-size:10px">Request a Quote</div>
<svg class="abs" style="top:583px;left:0" width="1200" height="82" viewBox="0 0 1200 82" preserveAspectRatio="none">
  <path d="M0 60 Q300 20 600 8 Q900 20 1200 60 L1200 82 L0 82 Z" fill="#fff"/>
</svg>

<!-- Feature circles -->
<div class="abs feature" style="top:714px;left:322px;background:var(--blue)">
  <svg width="52" height="52" viewBox="0 0 52 52" fill="none" stroke="#fff" stroke-width="2"><circle cx="26" cy="15" r="7"/><circle cx="12" cy="21" r="5"/><circle cx="40" cy="21" r="5"/><path d="M13 46V34a13 13 0 0 1 26 0v12M3 46V36a9 9 0 0 1 9-9M49 46V36a9 9 0 0 0-9-9"/></svg>
  Our Staff Is<br>The Difference<span class="chev"></span>
</div>
<div class="abs feature" style="top:714px;left:521px;background:var(--yellow)">
  <svg width="52" height="52" viewBox="0 0 52 52" fill="none" stroke="#fff" stroke-width="2"><rect x="10" y="8" width="32" height="40" rx="3"/><rect x="19" y="4" width="14" height="8" rx="2"/><path d="M17 22h18M17 30h18M17 38h12"/></svg>
  Top To Bottom<br>Service Options<span class="chev"></span>
</div>
<div class="abs feature" style="top:714px;left:719px;background:var(--orange)">
  <svg width="52" height="52" viewBox="0 0 52 52" fill="none" stroke="#fff" stroke-width="2"><path d="M6 14h14l4 5h22v25H6z"/><rect x="16" y="24" width="20" height="14" rx="2"/><path d="M22 24v-3h8v3"/></svg>
  Full Portfolio<br>Management<span class="chev"></span>
</div>

<!-- About -->
<div class="ph" role="img" aria-label="Cleaner vacuuming an office floor beside a yellow mop bucket" style="top:975px;left:176px;width:414px;height:414px;border-radius:50%;background:linear-gradient(160deg,#eef0f2,#c9ccd1 55%,#8f8e86)"></div>
<div class="abs eyebrow" style="top:1047px;left:635px">About Us</div>
<h2 class="abs about-title" style="top:1070px;left:635px">Harbor Tidy</h2>
<p class="abs body-text" style="top:1128px;left:635px;width:420px">Why scrambled text? That's exactly the point. By using text that's unreadable but maintains the general pattern of regular writing — including normal word length, spacing, and punctuation — designers can focus on the visual elements of a layout without the actual content getting in the way. The pseudo-Latin appearance...</p>
<div class="btn" style="top:1280px;left:637px;width:120px;height:35px;font-size:10.5px">Learn More</div>

<!-- Why choose us -->
<h2 class="abs about-title" style="top:1526px;left:94px">Why Choose Us?</h2>
<div class="abs why-item" style="top:1614px">
  <div class="ico" style="background:var(--orange)"><svg width="40" height="40" viewBox="0 0 40 40" fill="none" stroke="#fff" stroke-width="2"><circle cx="20" cy="20" r="15"/><path d="M20 10v10l7 5"/></svg></div>
  Reliable &amp; On-Time
</div>
<div class="abs why-item active" style="top:1704px">
  <div class="ico" style="background:var(--yellow)"><svg width="40" height="40" viewBox="0 0 40 40" fill="none" stroke="#fff" stroke-width="2"><circle cx="20" cy="20" r="15"/><path d="M7 16c6 0 8 4 12 2s6-8 10-6M12 33c2-6 8-6 10-10s6-2 10 2"/></svg></div>
  Eco-Friendly Cleaning
  <svg width="22" height="22" viewBox="0 0 22 22" style="margin-left:auto;margin-right:14px"><circle cx="11" cy="11" r="11" fill="#fff"/><path d="M9 7l4 4-4 4" stroke="#1f4fc3" stroke-width="2" fill="none"/></svg>
</div>
<div class="abs why-item" style="top:1798px">
  <div class="ico" style="background:var(--blue)"><svg width="40" height="40" viewBox="0 0 40 40" fill="none" stroke="#fff" stroke-width="2"><path d="M20 5l12 5v9c0 8-5 13-12 16C13 32 8 27 8 19v-9z"/><path d="M14 20l4 4 8-8"/></svg></div>
  Fully Insured &amp; Trained Staff
</div>
<div class="abs" style="top:1476px;left:648px;width:456px;height:456px;border-radius:50%;border:7px solid var(--yellow)"></div>
<div class="ph" role="img" aria-label="Carpet being deep cleaned with an extraction machine" style="top:1498px;left:670px;width:412px;height:412px;border-radius:50%;background:linear-gradient(160deg,#d6d8dc,#a7a9ad 55%,#6f7176)"></div>

<!-- Services -->
<svg class="abs" style="top:1995px;left:0" width="1200" height="760" viewBox="0 0 1200 760" preserveAspectRatio="none">
  <path d="M0 50 Q600 -20 1200 50 L1200 760 L0 760 Z" fill="#eef2f8"/>
</svg>
<h2 class="section-title" style="top:2134px">Our Cleaning Services</h2>
<p class="abs body-text" style="top:2202px;left:260px;width:680px;text-align:center;font-size:12.5px;line-height:21px">The short answer is that lorem ipsum text doesn't actually "say" anything meaningful. It's deliberately scrambled Latin that doesn't form coherent sentences. While it comes from Cicero's "De Finibus Bonorum et Malorum...</p>

<div class="abs card" style="left:61px"><h3>Office Cleaning</h3><span class="go"><svg width="12" height="12" viewBox="0 0 12 12"><path d="M2 10 10 2M4 2h6v6" stroke="#3aa55a" stroke-width="1.4" fill="none"/></svg></span><hr><p>Lorem ipsum is placeholder text used in design...</p><div class="ph" role="img" aria-label="Cleaner wiping an office desk" style="background:linear-gradient(160deg,#e9eef3,#b7c3cf)"></div></div>
<div class="abs card" style="left:336px"><h3>Construction Cleaning</h3><hr><p>Lorem ipsum is placeholder text used in design...</p><div class="ph" role="img" aria-label="Worker cleaning up a construction site" style="background:linear-gradient(160deg,#dfe2de,#8e948c)"></div><div class="abs" style="left:10px;bottom:14px;width:58px;height:58px;border-radius:12px;background:var(--orange);display:flex;align-items:center;justify-content:center"><svg width="26" height="26" viewBox="0 0 26 26"><path d="M5 21 21 5M9 5h12v12" stroke="#fff" stroke-width="2" fill="none"/></svg></div></div>
<div class="abs card" style="left:610px"><h3>Carpet Care</h3><span class="go"><svg width="12" height="12" viewBox="0 0 12 12"><path d="M2 10 10 2M4 2h6v6" stroke="#3aa55a" stroke-width="1.4" fill="none"/></svg></span><hr><p>Lorem ipsum is placeholder text used in design...</p><div class="ph" role="img" aria-label="Cleaner vacuuming a carpet beside a sofa" style="background:linear-gradient(160deg,#f0ede8,#c2bcb2)"></div></div>
<div class="abs card" style="left:884px"><h3>Glass Cleaning</h3><span class="go"><svg width="12" height="12" viewBox="0 0 12 12"><path d="M2 10 10 2M4 2h6v6" stroke="#3aa55a" stroke-width="1.4" fill="none"/></svg></span><hr><p>Lorem ipsum is placeholder text used in design...</p><div class="ph" role="img" aria-label="Cleaner washing a window" style="background:linear-gradient(160deg,#dfe6e4,#8e9a8f)"></div></div>
<div class="btn" style="top:2658px;left:515px;width:172px;height:35px;font-size:10.5px">View All Service</div>

<!-- How we work -->
<h2 class="section-title" style="top:2788px">How We Work</h2>
<svg class="abs" style="top:2855px;left:380px" width="440" height="430" viewBox="0 0 440 430"><path d="M216 6a208 208 0 1 1-170 336" fill="none" stroke="#222" stroke-width="2"/></svg>
<div class="ph" role="img" aria-label="Smiling cleaner in gloves wiping a glass window" style="top:2888px;left:94px;width:440px;height:434px;border-radius:46% 54% 48% 52% / 50% 44% 56% 50%;background:linear-gradient(150deg,#d3d6db,#8c9098 60%,#5b4d4a)"></div>
<div class="ph" role="img" aria-label="Bucket of cleaning supplies and spray bottles" style="top:3010px;left:540px;width:180px;height:150px;border-radius:30px;background:linear-gradient(160deg,#c9e4ff,#7fb6f0 50%,#ff8a4c)"></div>

<div class="abs step-ico" style="top:2876px;left:667px;background:var(--blue)"><svg width="38" height="38" viewBox="0 0 38 38" fill="none" stroke="#fff" stroke-width="2"><rect x="7" y="6" width="24" height="28" rx="3"/><circle cx="19" cy="20" r="6"/><path d="M16 20l2 2 4-4"/></svg></div>
<div class="abs step" style="top:2860px;left:778px"><h4>Assessment &amp; Quote</h4><p>Every great clean begins with understanding your space. Our team conducts a detailed walkthrough to identify key cleaning areas, traffic patterns...</p></div>
<div class="abs step-ico" style="top:3018px;left:747px;background:var(--yellow)"><svg width="38" height="38" viewBox="0 0 38 38" fill="none" stroke="#fff" stroke-width="2"><rect x="8" y="6" width="22" height="28" rx="3"/><path d="M13 14h12M13 20h12M13 26h8"/></svg></div>
<div class="abs step" style="top:3005px;left:854px"><h4>Quality Check &amp; Maintenance</h4><p style="width:250px">Quality doesn't stop when the job is done. Our supervisors perform regular inspections to maintain high standards and ensure client satisfaction...</p></div>
<div class="abs step-ico" style="top:3162px;left:698px;background:var(--orange)"><svg width="38" height="38" viewBox="0 0 38 38" fill="none" stroke="#fff" stroke-width="2"><path d="M6 18 19 7l13 11M10 15v17h18V15"/><rect x="16" y="22" width="6" height="10"/></svg></div>
<div class="abs step" style="top:3176px;left:809px"><h4>Professional Cleaning</h4><p style="width:250px">Once approved, our trained and uniformed staff arrive on schedule, fully equipped with professional-grade tools and eco-friendly cleaning...</p></div>

<!-- Testimonials -->
<svg class="abs" style="top:3404px;left:556px" width="88" height="58" viewBox="0 0 88 58"><g fill="#f04a1c"><path d="M4 36C4 16 16 4 34 2v10c-9 2-14 8-14 14a16 16 0 1 1-16 10z"/><path d="M48 36C48 16 60 4 78 2v10c-9 2-14 8-14 14a16 16 0 1 1-16 10z"/></g></svg>
<h2 class="section-title" style="top:3470px">What Our Clients Say</h2>
<p class="abs" style="top:3527px;left:240px;width:720px;text-align:center;font-style:italic;font-size:16px;line-height:27px;color:var(--text)">The short answer is that lorem ipsum text doesn't actually "say" anything meaningful. It's deliberately scrambled Latin that doesn't form coherent sentences. While it comes from Cicero's "De Finibus Bonorum et Malorum...</p>
<div class="abs" style="top:3625px;left:0;width:1200px;text-align:center;font-weight:600;font-size:14px">Dana R., Business Owner</div>
<div class="abs" style="top:3680px;left:580px;display:flex;gap:6px"><i style="width:11px;height:11px;border-radius:50%;background:#9fb4e6"></i><i style="width:11px;height:11px;border-radius:50%;background:var(--blue)"></i><i style="width:11px;height:11px;border-radius:50%;background:#9fb4e6"></i></div>

<!-- Contact -->
<h2 class="section-title" style="top:3755px">Contact Us</h2>
<div class="field" style="top:3825px;left:271px;width:158px">First Name*</div>
<div class="field" style="top:3825px;left:437px;width:158px">Last Name*</div>
<div class="field" style="top:3825px;left:603px;width:160px">Phone</div>
<div class="field" style="top:3825px;left:771px;width:160px">Email*</div>
<div class="field" style="top:3881px;left:271px;width:660px;height:131px;border-radius:18px">Message</div>
<div class="abs" style="top:4026px;left:0;width:1200px;display:flex;justify-content:center;align-items:center;gap:10px;font-size:10.5px;font-weight:500">
  Would You Like To Receive Emails From us in the Future?*
  <span style="display:flex;align-items:center;gap:4px;margin-left:8px"><i style="width:13px;height:13px;border:1px solid #888;border-radius:50%"></i>YES</span>
  <span style="display:flex;align-items:center;gap:4px;margin-left:8px"><i style="width:13px;height:13px;border:1px solid #888;border-radius:50%"></i>NO</span>
</div>
<div class="btn" style="top:4074px;left:525px;width:150px;height:36px;font-size:11px">Submit Now</div>

<!-- Footer -->
<svg class="abs" style="top:4190px;left:0" width="1200" height="62" viewBox="0 0 1200 62" preserveAspectRatio="none">
  <path d="M0 62 L0 40 Q600 -20 1200 40 L1200 62 Z" fill="#1f4fc3"/>
</svg>
<footer class="abs footer"></footer>
<div class="abs brand" style="top:4392px;left:90px">
  <div class="brand-dot"></div>
  <div class="brand-name" style="color:var(--white);font-size:18px">HARBOR TIDY TEAM</div>
</div>
<div class="abs f-head" style="top:4338px;left:393px">Contact Us</div>
<div class="abs f-row" style="top:4395px;left:393px"><span class="f-ico"><svg width="12" height="12" viewBox="0 0 24 24"><path d="M6.6 10.8a15 15 0 0 0 6.6 6.6l2.2-2.2c.3-.3.7-.4 1-.2 1.1.4 2.3.6 3.6.6.6 0 1 .4 1 1V20c0 .6-.4 1-1 1A17 17 0 0 1 3 4c0-.6.4-1 1-1h3.5c.6 0 1 .4 1 1 0 1.3.2 2.5.6 3.6.1.3 0 .7-.2 1z" fill="#fff"/></svg></span>(123) 456-7890</div>
<div class="abs f-row" style="top:4440px;left:393px"><span class="f-ico"><svg width="12" height="12" viewBox="0 0 24 24" fill="none" stroke="#fff" stroke-width="2.4"><rect x="3" y="5" width="18" height="14" rx="2"/><path d="m3 7 9 6 9-6"/></svg></span>info@harbortidyteam.com</div>
<div class="abs f-head" style="top:4338px;left:726px">Newsletter</div>
<p class="abs" style="top:4392px;left:726px;width:390px;font-size:13px;line-height:19px;color:var(--white)">Subscribe to our newsletter to receive updates on new product offerings...</p>
<div class="abs" style="top:4453px;left:726px;width:385px;height:44px;border-radius:22px;background:var(--white);display:flex;align-items:center;padding:0 24px;font-size:12px;color:#555">Enter Your Email Address...
  <svg width="20" height="20" viewBox="0 0 24 24" style="margin-left:auto"><path d="M2 11 22 3l-7 19-3-8z" fill="#f04a1c"/></svg>
</div>
<div class="abs" style="top:4585px;left:90px;width:1022px;height:1px;background:rgba(255,255,255,.45)"></div>
<div class="abs" style="top:4609px;left:0;width:1200px;text-align:center;font-size:13px;color:var(--white)">©Copyright 2025 Harbor Tidy Team. All Rights Reserved.</div>
<div class="abs" style="top:4561px;left:1131px;width:48px;height:48px;border-radius:50%;background:var(--orange);display:flex;align-items:center;justify-content:center"><svg width="14" height="14" viewBox="0 0 14 14"><path d="M3 9l4-4 4 4" stroke="#fff" stroke-width="2" fill="none"/></svg></div>

</body>
</html>
```